Quillbrookes websites redesign

Www.quill-brookes.com needs to be redesigned along with updations. The incremental material will be provided for the updations. We are looking for complete redesign of the pages with the new content. The complete write up will be provided soon

Target Market(s)

Global

Coding

Coded - Design and coding required

Number of Pages Required

5+ page

Requirements
Must have
• A clean and slick design for the Consulting.
Should not have
• Too many pictures which reduces the speed of the site

```html
<!DOCTYPE html>
<html lang="en">
<head>
<meta charset="utf-8">
<title>Quillbrookes – Consultancy</title>
<link href="https://fonts.googleapis.com/css2?family=Arimo:wght@400;700&family=Montserrat:wght@400;600&family=Raleway:wght@300&display=swap" rel="stylesheet">
<style>
:root{
  --blue:#2a9bc8;
  --map:#33a0c9;
  --ink:#3a3a3a;
  --text:#555;
  --muted:#777;
  --rule:#d6d6d6;
  --hero:#f1f1f1;
  --footer:#151515;
  --footer-text:#9a9a9a;
  --white:#fff;
}
*{margin:0;padding:0;box-sizing:border-box}
html,body{width:858px;height:1200px;overflow:hidden;background:var(--white)}
body{position:relative;font-family:Arimo,Arial,sans-serif;color:var(--text)}
.abs{position:absolute}
.site-header{position:absolute;left:0;top:0;width:858px;height:45px;border-bottom:1px solid #e6e6e6;background:var(--white)}
.brand{position:absolute;left:193px;top:11px;display:flex;align-items:center;gap:6px;font-family:Montserrat,sans-serif;font-weight:600;font-size:15px;color:#5a2a2a}
.brand i{width:18px;height:18px;border-radius:50%;background:#5a2a2a;display:block}
.nav{position:absolute;top:19px;font-family:Arimo,sans-serif;font-size:7px;color:#666}
.nav.active{color:var(--blue)}
.nav-underline{position:absolute;left:497px;top:42px;width:35px;height:2px;background:var(--blue)}
.hero{position:absolute;left:0;top:45px;width:858px;height:256px;background:var(--hero)}
.hero-title{position:absolute;left:0;width:858px;top:84px;text-align:center;font-family:Raleway,sans-serif;font-weight:300;font-size:16px;color:#555}
.map{position:absolute;left:268px;top:127px;width:304px;height:148px;background:linear-gradient(180deg,#38a6cf,#2d95bf);border-radius:40px 60px 30px 50px}
.geo-label{position:absolute;font-size:5.6px;color:#444;white-space:nowrap}
.heading{position:absolute;font-family:Montserrat,sans-serif;font-size:10px;color:var(--ink);letter-spacing:.1px}
.heading b{font-weight:600}
.copy{position:absolute;font-size:5.9px;line-height:9.6px;color:var(--text)}
.copy a,.link{color:var(--blue);text-decoration:none}
.photo{position:absolute;width:172px;height:100px}
.rule{position:absolute;left:193px;width:472px;height:1px;background:var(--rule)}
.ticks{position:absolute;list-style:none;font-size:5.9px;color:var(--text);line-height:9.6px}
.ticks li{position:relative;padding-left:13px}
.ticks li::before{content:"";position:absolute;left:1px;top:2px;width:4px;height:2px;border-left:1.3px solid #444;border-bottom:1.3px solid #444;transform:rotate(-45deg)}
.site-footer{position:absolute;left:0;top:1012px;width:858px;height:188px;background:var(--footer);color:var(--footer-text);font-size:6.2px}
.footer-brand{position:absolute;left:194px;top:36px;display:flex;align-items:center;gap:5px;font-family:Montserrat,sans-serif;font-size:12px;color:#aaa}
.footer-brand i{width:15px;height:15px;border-radius:50%;background:#777;display:block}
.f-title{position:absolute;top:36px;font-family:Montserrat,sans-serif;font-size:7.2px;color:#e5e5e5;letter-spacing:.3px}
.f-title::after{content:"";position:absolute;left:0;top:14px;width:15px;height:1px;background:#888}
.f-lines{position:absolute;line-height:10.3px}
.strong-blue{color:var(--blue);font-weight:700}
.f-mail{color:var(--blue);text-decoration:underline}
.field{position:absolute;left:345px;top:78px;width:108px;height:20px;border:1px solid #555;padding:6px 7px;font-size:6px;color:#bbb}
.field span{position:absolute;right:5px;top:6px;width:8px;height:6px;background:var(--blue);border-radius:1px}
.site-links{position:absolute;left:498px;top:60px;list-style:none;line-height:12.9px;font-size:6.2px;color:#aaa}
.site-links li::before{content:"» ";color:var(--blue)}
.site-links .current{color:var(--blue);text-decoration:underline}
.social{position:absolute;top:62px;width:15px;height:15px;border-radius:50%;border:1.2px solid #bbb}
.social.first{background:var(--blue);border-color:#ddd}
.footer-rule{position:absolute;left:0;top:160px;width:858px;height:1px;background:#2b2b2b}
.copyright{position:absolute;left:194px;top:173px;font-size:6px;color:#888}
</style>
</head>
<body>

<header class="site-header">
  <div class="brand"><i></i>Quillbrookes</div>
  <span class="nav" style="left:417px">home</span>
  <span class="nav" style="left:455px">founder</span>
  <span class="nav active" style="left:496px">consultancy</span>
  <span class="nav" style="left:549px">platform</span>
  <span class="nav" style="left:588px">case studies</span>
  <span class="nav" style="left:642px">contact</span>
  <div class="nav-underline"></div>
</header>

<section class="hero">
  <h1 class="hero-title" style="top:39px">Geographical Reach – Corporate Deals Placed</h1>
</section>
<div class="map" role="img" aria-label="World map in blue showing regions where corporate deals were placed"></div>
<svg class="abs" style="left:0;top:0" width="858" height="300" aria-hidden="true">
  <g stroke="#222" stroke-width=".6" fill="#111">
    <line x1="254" y1="172" x2="305" y2="172"/><circle cx="305" cy="172" r="1.8"/>
    <line x1="375" y1="180" x2="402" y2="180"/><circle cx="402" cy="180" r="1.8"/>
    <line x1="382" y1="189" x2="448" y2="188"/><circle cx="448" cy="188" r="1.8"/>
    <line x1="452" y1="193" x2="530" y2="193"/><circle cx="452" cy="193" r="1.8"/>
    <line x1="518" y1="185" x2="542" y2="184"/><circle cx="518" cy="185" r="1.8"/>
    <line x1="506" y1="208" x2="548" y2="208"/><circle cx="506" cy="208" r="1.8"/>
  </g>
</svg>
<span class="geo-label" style="left:230px;top:169px">US 10.0</span>
<span class="geo-label" style="left:338px;top:177px">Morocco 8.4</span>
<span class="geo-label" style="left:347px;top:186px">Kuwait 80.0</span>
<span class="geo-label" style="left:546px;top:181px">Hong Kong 13.0</span>
<span class="geo-label" style="left:532px;top:190px">Dubai 27.6</span>
<span class="geo-label" style="left:551px;top:205px">Singapore 6.0</span>

<section class="service bank">
  <div class="photo" style="left:193px;top:331px;background:linear-gradient(120deg,#a9c3dc,#dfe9f2 60%,#f3dde2)" role="img" aria-label="Hand dropping a banknote into a pink piggy bank"></div>
  <h2 class="heading" style="left:388px;top:329px">BANK <b>CONSULTANCY</b></h2>
  <p class="copy" style="left:388px;top:356px;width:277px">Capacity Building for Trade Finance either through Export Credit Insurance/ Developmental Financial Institution and Private Risk Insurance from a Risk and Marketing Perspective.</p>
  <p class="copy" style="left:388px;top:386px;width:277px">Arrangement of Long term liability from alternate sources of liquidity for onlending purposes to emerging country banks.</p>
</section>
<div class="rule" style="top:460px"></div>

<section class="service vanilla">
  <h2 class="heading" style="left:193px;top:489px">CONSULTANCY - <b>PLAIN VANILLA FINANCING SOLUTIONS</b></h2>
  <p class="copy" style="left:193px;top:517px;width:277px">The Consultancy provides access to local/regional banks across Hong Kong, Singapore, Dubai , New York and London and helps corporate clients in diversifying their financial partners and adding new banks to their bank group. The Consultancy provides Trade finance solutions for working capital requirements and assists in arranging External Commercial Borrowings/Foreign Currency Term Loans for long-term requirements. <a href="#">Our main areas of expertise:</a></p>
  <ul class="ticks" style="left:193px;top:582px;width:290px">
    <li style="margin-bottom:7.6px">Introduction of regional bank for Subsidiaries /Joint Ventures across the world</li>
    <li style="margin-bottom:7.6px">Plain-vanilla working capital lines from banks – Letter of Credit, Trust Receipt, Bill Discounting, etc</li>
    <li style="margin-bottom:7.6px">Arranging External Commercial Borrowings/Foreign Currency Term Loans for long-term requirement</li>
    <li style="margin-bottom:7.6px">Providing efficiency in terms of better leverage and pricing through new lenders</li>
    <li>Bank line business like Guarantee issuance and LC confirmations over longer tenor</li>
  </ul>
  <div class="photo" style="left:493px;top:491px;background:linear-gradient(135deg,#6f7a7e,#d9dde0 45%,#eef0f1)" role="img" aria-label="Calculator, glasses and a pen over printed financial charts"></div>
</section>
<div class="rule" style="top:690px"></div>

<section class="service structured">
  <div class="photo" style="left:193px;top:727px;background:linear-gradient(110deg,#c9a98a,#e8dccd 55%,#f2e6e6)" role="img" aria-label="Smiling businesswoman with colleagues working in the background"></div>
  <h2 class="heading" style="left:387px;top:724px">CONSULTANCY - <b>STRUCTURED FINANCING SOLUTIONS*</b></h2>
  <p class="copy" style="left:388px;top:752px;width:277px">The Consultancy provides end-to-end structured solutions on the Payables, Receivables or Inventory side for working capital requirements with off/part/on recourse balance sheet structures. We also specialize in providing credit enhancements through private or sovereign Insurance market to enhance the rating of a debt paper and improve distribution and market appetite.</p>
  <p class="copy" style="left:388px;top:800px;width:277px">On the term side, the Consultancy focuses on providing access to alternate liquidity providers like Developmental Financial Institutions, Export Credit Agency and Hedge Funds for both corporates and banks<br>The Consultancy through varied structure can also assist in monetization of unfunded bank lines for arranging financing. <a href="#">The following are our main areas of expertise:</a></p>
  <ul class="ticks" style="left:387px;top:863px;width:280px">
    <li style="margin-bottom:8px">Structured working capital solutions – like back-to-back LC, front-to-back LC, etc.</li>
    <li style="margin-bottom:8px">Export prepayments - Pre-export unsecured advance against contracts/open account/LC with the Buyers. This significantly reduces the working capital utilisation of most companies</li>
    <li style="margin-bottom:8px">Structured project financing through Export Credit Agencies and Developmental Financial Institutions - Direct credit limit on the projects can be looked into either with a single DFI or with a consortium of ECA/DFI's which makes the project significantly scalable</li>
    <li>Recourse/ part recourse/ non-recourse receivables financing – with or without credit enhancements</li>
  </ul>
</section>

<footer class="site-footer">
  <div class="footer-brand"><i></i>Quillbrookes</div>
  <div class="f-lines" style="left:194px;top:62px">Quillbrookes Consultancy Ltd<br>Suite 4, 9th Floor, Harbourgate Tower<br>22 Linden Quay Road, Kowloon<br>Hong Kong</div>
  <div class="f-lines" style="left:194px;top:112px">T: <span class="strong-blue">852-20004417</span><br>E: <span class="f-mail">query@quill-brookes.com</span></div>

  <h3 class="f-title" style="left:345px">GET IN TOUCH!</h3>
  <div class="f-lines" style="left:345px;top:61px">Simply Drop Your Mail Here</div>
  <div class="field">Your Email Here<span></span></div>

  <h3 class="f-title" style="left:498px">SITE LINKS</h3>
  <ul class="site-links">
    <li><span class="current">Home</span></li>
    <li>Founder</li>
    <li>Consultancy</li>
    <li>System</li>
    <li>Case Studies</li>
    <li>Contact</li>
  </ul>

  <h3 class="f-title" style="left:597px">SOCIAL LINKS</h3>
  <span class="social first" style="left:598px"></span>
  <span class="social" style="left:616px"></span>
  <span class="social" style="left:633px"></span>
  <span class="social" style="left:650px"></span>

  <div class="footer-rule"></div>
  <p class="copyright">© Quillbrookes Consultancy Limited</p>
</footer>

</body>
</html>
```